Business card design for my company.
I would like the card's background colour to be black. You can also see our web site to get an idea of our brand. https://www.tmwhomecrafting.com.au/
- Name
- Email

```html
<!DOCTYPE html>
<html lang="en">
<head>
<meta charset="utf-8">
<title>TMW Home Crafting – Business Card</title>
<link rel="stylesheet" href="https://fonts.googleapis.com/css2?family=Montserrat:ital,wght@0,400;0,600;1,400&family=Roboto:wght@300;400&display=swap">
<style>
  :root {
    --page-bg: #1d1e20;
    --card-bg: #3a3b3d;
    --ink: #ffffff;
    --ink-soft: #e3e3e3;
    --rule: #cfcfcf;
    --accent: #1e9b47;
  }
  * { margin: 0; padding: 0; box-sizing: border-box; }
  html, body {
    width: 1200px; height: 1043px; overflow: hidden;
    background: var(--page-bg);
  }
  .canvas { position: relative; width: 1200px; height: 1043px; }

  .card {
    position: absolute; left: 210px; width: 780px; height: 436px;
    background: var(--card-bg);
    box-shadow: 0 8px 24px rgba(0,0,0,.45);
  }
  .card--front { top: 100px; }
  .card--back { top: 580px; }

  /* Front */
  .brand-mark {
    position: absolute; left: 51px; top: 40px;
    display: flex; align-items: center; gap: 8px;
    font-family: "Montserrat", sans-serif; font-weight: 600;
    font-size: 26px; color: var(--ink); letter-spacing: 1px;
  }
  .brand-mark__square { width: 12px; height: 12px; background: var(--accent); }

  .headline {
    position: absolute; right: 43px; top: 58px;
    font-family: "Montserrat", sans-serif; font-style: italic; font-weight: 400;
    font-size: 30px; letter-spacing: 3px; color: var(--ink);
  }
  .person { position: absolute; right: 40px; top: 186px; text-align: right; }
  .person__name {
    font-family: "Montserrat", sans-serif; font-size: 31px; color: var(--ink); line-height: 1;
  }
  .person__first { color: var(--accent); }
  .person__role {
    font-family: "Roboto", sans-serif; font-size: 17px; color: var(--ink-soft); margin-top: 4px;
  }
  .person-tab {
    position: absolute; right: -6px; top: 192px; width: 12px; height: 42px; background: var(--accent);
  }
  .divider {
    position: absolute; left: 51px; top: 300px; width: 684px; height: 2px; background: var(--rule);
  }
  .contact-list {
    position: absolute; left: 52px; top: 326px; list-style: none;
    font-family: "Roboto", sans-serif; font-weight: 300; font-size: 18px; color: var(--ink);
  }
  .contact-list li { display: flex; align-items: center; gap: 12px; height: 22px; }
  .contact-list svg { width: 14px; height: 14px; fill: var(--accent); }

  /* Back */
  .brand-lockup {
    position: absolute; left: 0; right: 0; top: 190px;
    display: flex; justify-content: center; align-items: center; gap: 14px;
    font-family: "Montserrat", sans-serif; font-weight: 600;
    font-size: 46px; color: var(--ink); letter-spacing: 1px;
  }
  .brand-lockup__square { width: 22px; height: 22px; background: var(--accent); }

  .web-row {
    position: absolute; left: 39px; right: 39px; top: 384px;
    display: flex; align-items: center; gap: 14px;
    font-family: "Roboto", sans-serif; font-size: 19px; color: var(--ink);
  }
  .web-row__line { flex: 1; height: 2px; background: var(--rule); }
  .web-row__domain { color: var(--accent); }
</style>
</head>
<body>
<main class="canvas">
  <section class="card card--front">
    <div class="brand-mark"><span class="brand-mark__square"></span>TMW</div>
    <h1 class="headline">HOME CRAFTING</h1>
    <div class="person">
      <p class="person__name"><span class="person__first">Liam</span> Harper</p>
      <p class="person__role">General Manager</p>
    </div>
    <span class="person-tab"></span>
    <span class="divider"></span>
    <ul class="contact-list">
      <li><svg viewBox="0 0 24 24"><path d="M6.6 10.8a15 15 0 0 0 6.6 6.6l2.2-2.2c.3-.3.7-.4 1-.2 1.1.4 2.3.6 3.6.6.6 0 1 .4 1 1V20c0 .6-.4 1-1 1A17 17 0 0 1 3 4c0-.6.4-1 1-1h3.5c.6 0 1 .4 1 1 0 1.3.2 2.5.6 3.6.1.3 0 .7-.2 1z"/></svg>0400 123 456</li>
      <li><svg viewBox="0 0 24 24"><path d="M2 5h20v14H2z M2 5l10 7 10-7" /></svg>info@tmwhomecrafting.com.au</li>
      <li><svg viewBox="0 0 24 24"><path d="M12 2a7 7 0 0 0-7 7c0 5 7 13 7 13s7-8 7-13a7 7 0 0 0-7-7zm0 9.5A2.5 2.5 0 1 1 12 6.5a2.5 2.5 0 0 1 0 5z"/></svg>Riverton, Tasmania, Australia</li>
    </ul>
  </section>

  <section class="card card--back">
    <div class="brand-lockup"><span class="brand-lockup__square"></span>TMW Home Crafting</div>
    <div class="web-row">
      <span class="web-row__line"></span>
      <span>www.<span class="web-row__domain">tmwhomecrafting</span>.com.au</span>
      <span class="web-row__line"></span>
    </div>
  </section>
</main>
</body>
</html>
```